Designing a Chocolate Bar's Package

We are a chocolate manufacturing company located in Lebanon. We produce chocolate on a wholesale level, and we are planning a new line of production at the moment.
We intend to be make small chocolate bars (about 30g) similar to the "Varnou Classica" bar with several flavors. 2 flavors have been decided so far (Mint flavored dark chocolate and Plain dark chocolate).
The packaging material will be similar to varnou's package as well. It won't be a carton box. It'll be some sort of paper wrapping the entire bar. So I am looking for a design that has a unique and cool front and back look.
If only one design is to be prepared, please choose either the mint's flavor or the plain dark chocolate, and prepare the design accordingly.
Updates
Project Deadline Extended
Reason: I still have some time to begin the production. The new deadline,therefore, is the end of this month.
Target Market(s)
basically all chocolate lovers...
Industry/Entity Type
It Company
Requirements
Must have
- I will be uploading our logo. Please make sure to use it in the design.

```html
<!DOCTYPE html>
<html lang="en">
<head>
<meta charset="utf-8">
<title>Cardello Dark Chocolate Wrappers</title>
<link rel="stylesheet" href="https://fonts.googleapis.com/css2?family=Yellowtail&family=Parisienne&family=Roboto:wght@400&display=swap">
<style>
  :root {
    --backdrop: #e4e5e7;
    --gold-light: #f1dcaa;
    --gold: #c9a15a;
    --gold-dark: #9c7636;
    --paper: #ffffff;
    --brand-brown: #5b3620;
    --tagline-gold: #b58a45;
    --mint-deep: #173c17;
    --mint-mid: #2c6a22;
    --mint-glow: #7db53d;
    --mint-stripe: #8cc63f;
    --plain-deep: #3d0f06;
    --plain-mid: #8a2a0d;
    --plain-glow: #f06a24;
    --plain-stripe: #ee5a22;
    --cocoa-dark: #1e0f0a;
    --cocoa-mid: #3b2017;
    --label-white: #ffffff;
  }
  * { box-sizing: border-box; margin: 0; padding: 0; }
  html, body { width: 1162px; height: 1200px; overflow: hidden; }
  body { background: var(--backdrop); position: relative; }

  .wrapper {
    position: absolute;
    top: 100px;
    width: 448px;
    height: 1006px;
    display: flex;
    flex-direction: column;
    overflow: hidden;
    border-radius: 4px;
  }
  .wrapper--mint { left: 116px; }
  .wrapper--plain { left: 598px; }

  .wrapper::after {
    content: "";
    position: absolute; inset: 0;
    pointer-events: none;
    background: linear-gradient(90deg,
      rgba(0,0,0,0.28) 0%, rgba(0,0,0,0.05) 5%, rgba(255,255,255,0.12) 9%,
      rgba(255,255,255,0) 16%, rgba(255,255,255,0) 84%,
      rgba(255,255,255,0.12) 91%, rgba(0,0,0,0.05) 95%, rgba(0,0,0,0.28) 100%);
  }

  .gold-seal {
    height: 16px;
    background: linear-gradient(180deg, var(--gold-light), var(--gold) 55%, var(--gold-dark));
  }

  .brand-panel {
    height: 302px;
    background: var(--paper);
    text-align: center;
    padding-top: 42px;
  }
  .brand-name {
    font-family: "Yellowtail", cursive;
    font-size: 104px;
    line-height: 1;
    color: var(--brand-brown);
  }
  .brand-tagline {
    font-family: "Parisienne", cursive;
    font-size: 34px;
    color: var(--tagline-gold);
    margin-top: 18px;
  }

  .flavor-stripe { height: 13px; }
  .wrapper--mint .flavor-stripe { background: var(--mint-stripe); }
  .wrapper--plain .flavor-stripe { background: var(--plain-stripe); }

  .flavor-panel {
    flex: 1;
    position: relative;
    text-align: center;
    color: var(--label-white);
  }
  .wrapper--mint .flavor-panel {
    background: radial-gradient(ellipse 70% 45% at 50% 48%, var(--mint-glow) 0%, var(--mint-mid) 50%, var(--mint-deep) 100%);
  }
  .wrapper--plain .flavor-panel {
    background: radial-gradient(ellipse 70% 45% at 50% 48%, var(--plain-glow) 0%, var(--plain-mid) 55%, var(--plain-deep) 100%);
  }

  .product-photo {
    position: absolute;
    left: 84px; top: 30px;
    width: 280px; height: 430px;
    border-radius: 6px;
    background: linear-gradient(160deg, var(--cocoa-mid) 0%, var(--cocoa-dark) 100%);
  }

  .flavor-label {
    position: absolute;
    left: 0; right: 0; top: 482px;
  }
  .flavor-name {
    font-family: "Yellowtail", cursive;
    font-size: 33px;
    line-height: 1;
  }
  .product-name {
    font-family: "Yellowtail", cursive;
    font-size: 50px;
    line-height: 1;
    margin-top: 10px;
  }
  .net-weight {
    font-family: "Roboto", sans-serif;
    font-size: 30px;
    margin-top: 22px;
  }
</style>
</head>
<body>
  <article class="wrapper wrapper--mint">
    <div class="gold-seal"></div>
    <header class="brand-panel">
      <p class="brand-name">Cardello</p>
      <p class="brand-tagline">Quality Chocolate</p>
    </header>
    <div class="flavor-stripe"></div>
    <section class="flavor-panel">
      <div class="product-photo" role="img" aria-label="Stack of dark chocolate squares with a sprig of fresh mint leaves"></div>
      <div class="flavor-label">
        <p class="flavor-name">mint flavored</p>
        <p class="product-name">Dark Chocolate</p>
        <p class="net-weight">30g</p>
      </div>
    </section>
    <div class="gold-seal"></div>
  </article>

  <article class="wrapper wrapper--plain">
    <div class="gold-seal"></div>
    <header class="brand-panel">
      <p class="brand-name">Cardello</p>
      <p class="brand-tagline">Quality Chocolate</p>
    </header>
    <div class="flavor-stripe"></div>
    <section class="flavor-panel">
      <div class="product-photo" role="img" aria-label="Stack of plain dark chocolate squares"></div>
      <div class="flavor-label">
        <p class="flavor-name">plain</p>
        <p class="product-name">Dark Chocolate</p>
        <p class="net-weight">30g</p>
      </div>
    </section>
    <div class="gold-seal"></div>
  </article>
</body>
</html>
```